Local massage therapist needs some new marketing material

Hi there! I am a massage therapist here in Denver, CO in Alder Bend(shopping and art district) of the city. My business is called Lumo Bodywork of Denver. My practice has an eastern influence and I do reflexology, thai massage and use Chinese herbs, etc. I know all my clients and pay close attention to details. I am also very respectful of tradition and it shows in how I work. I tend to like modern, clean, fun, Asian designs. I am wanting a new business card and brochure. I have a logo and branding for my business that I want used in the design. Currently, the sign for my building is purple and I think my logo was designed to be purple. I will attach pictures of it and can send whatever files are necessary so it can be integrated into the brochure, etc. I like the purple but open to using other colors as well. Thanks!
My website is lumobodyworkofdenver.example where info can be gathered about me and services/fees for brochure.
Updates

Just increased budget. Please see new feedback in discussion thread.

Thanks!

                                       HEY ALL,

Just wanted to let you know that I made a change to my website. It is on the Prices Page. I no longer have the frequent  flyer prices but I added discounts. Let me know if you have any questions. Thanks so much!

Target Market(s)

healthy, urban, educated, upper middle class, yogis

Industry/Entity Type

Marketing

Requirements
Must have
• logo stays purple
Should not have
• not too busy

```html
<!DOCTYPE html>
<html lang="en">
<head>
<meta charset="utf-8">
<title>Lumo Bodywork of Denver – Business Card</title>
<link rel="stylesheet" href="https://fonts.googleapis.com/css2?family=Open+Sans:ital,wght@0,400;0,600;0,700;1,400&display=swap">
<style>
  :root {
    --purple: #6a2d91;
    --white: #ffffff;
    --ink: #555559;
    --muted: #77777b;
    --line: #9a9a9e;
    --backdrop: #e4e4ea;
  }
  * { box-sizing: border-box; margin: 0; padding: 0; }
  html, body { width: 1200px; height: 987px; overflow: hidden; }
  body {
    background: var(--backdrop);
    font-family: "Open Sans", Arial, sans-serif;
    display: flex; flex-direction: column; align-items: center; justify-content: center; gap: 40px;
  }
  .card {
    position: relative; width: 760px; height: 434px;
    background: var(--white); border-radius: 26px; overflow: hidden;
    box-shadow: 0 6px 18px rgba(0,0,0,0.12);
  }
  .brand {
    display: flex; align-items: center; gap: 14px;
    color: var(--purple); font-weight: 600; letter-spacing: 6px;
  }
  .brand-dot { width: 30px; height: 30px; border-radius: 50%; background: var(--purple); }
  .brand-name { font-size: 62px; line-height: 1; }

  /* front */
  .front .brand { position: absolute; left: 280px; top: 70px; }
  .front .band {
    position: absolute; left: 0; right: 0; top: 170px; height: 170px;
    background: var(--purple); color: var(--white);
    display: flex; align-items: center; padding-left: 60px;
  }
  .person { text-align: right; padding-right: 22px; border-right: 1px solid rgba(255,255,255,0.6); }
  .person-name { font-size: 26px; font-weight: 600; }
  .person-title { font-size: 18px; }
  .contacts { list-style: none; padding-left: 22px; font-size: 22px; line-height: 1.45; }
  .contacts li { display: flex; align-items: center; gap: 8px; }
  .contacts svg { width: 18px; height: 18px; fill: var(--white); flex: none; }
  .address { position: absolute; left: 60px; top: 362px; font-size: 20px; color: var(--ink); }

  /* back */
  .back { padding: 34px 44px; color: var(--ink); }
  .appt-title { color: var(--purple); font-weight: 700; font-size: 18px; margin-bottom: 22px; }
  .field { display: flex; align-items: flex-end; font-size: 19px; margin-bottom: 16px; }
  .field .rule { border-bottom: 1px dotted var(--line); height: 1px; margin: 0 8px 5px; }
  .hours { font-size: 19px; line-height: 1.45; margin-top: 18px; }
  .note { font-style: italic; font-size: 17px; color: var(--muted); margin-top: 10px; }
  .back .brand { position: absolute; right: 44px; top: 240px; }
  .back .brand-name { font-size: 54px; }
</style>
</head>
<body>
  <section class="card front" aria-label="Business card front">
    <div class="brand"><span class="brand-dot"></span><span class="brand-name">LUMO</span></div>
    <div class="band">
      <div class="person">
        <div class="person-name">Your Name</div>
        <div class="person-title">Title</div>
      </div>
      <ul class="contacts">
        <li><svg viewBox="0 0 24 24"><path d="M6.6 10.8a15 15 0 0 0 6.6 6.6l2.2-2.2c.3-.3.7-.4 1-.2 1.1.4 2.3.6 3.6.6.6 0 1 .4 1 1V20c0 .6-.4 1-1 1A17 17 0 0 1 3 4c0-.6.4-1 1-1h3.5c.6 0 1 .4 1 1 0 1.3.2 2.5.6 3.6.1.3 0 .7-.2 1z"/></svg>303.555.0188</li>
        <li><svg viewBox="0 0 24 24"><path d="M2 5h20v14H2zm2 2v.5l8 5 8-5V7l-8 5z"/></svg>info@lumobodyworkofdenver.example</li>
        <li><svg viewBox="0 0 24 24"><path d="M12 2a10 10 0 1 0 0 20 10 10 0 0 0 0-20zm0 2c.9 1.2 1.6 2.6 2 4h-4c.4-1.4 1.1-2.8 2-4zM4.3 14a8 8 0 0 1 0-4h3.4a16 16 0 0 0 0 4zm.8 2h3c.3 1.3.8 2.5 1.4 3.6A8 8 0 0 1 5.1 16zm3-8h-3a8 8 0 0 1 4.4-3.6C8.9 5.5 8.4 6.7 8.1 8zM12 20c-.9-1.2-1.6-2.6-2-4h4c-.4 1.4-1.1 2.8-2 4zm2.3-6H9.7a14 14 0 0 1 0-4h4.6a14 14 0 0 1 0 4zm.2 5.6c.6-1.1 1.1-2.3 1.4-3.6h3a8 8 0 0 1-4.4 3.6zm1.8-5.6a16 16 0 0 0 0-4h3.4a8 8 0 0 1 0 4z"/></svg>www.lumobodyworkofdenver.example</li>
      </ul>
    </div>
    <p class="address">1480 E Alder St, Denver, CO 80206</p>
  </section>

  <section class="card back" aria-label="Business card back">
    <h2 class="appt-title">YOUR APPOINTMENT</h2>
    <div class="field">Name :<span class="rule" style="width:360px"></span></div>
    <div class="field">Date :<span class="rule" style="width:150px"></span>Time :<span class="rule" style="width:170px"></span>am / pm</div>
    <p class="hours">Tues - Fri 10am - 8pm Sat 10am-5pm<br>(Appointments required) No walk-ins please.</p>
    <p class="note">We appreciate a 24 hr. notice for cancellations</p>
    <div class="brand"><span class="brand-dot"></span><span class="brand-name">LUMO</span></div>
  </section>
</body>
</html>
```